Landscape Construction and Design Company

We are a landscape construction and design company from New Jersey. We design and install landscapes and hardscapes for residential properties. The name of the company is Belwick's Landscape and Design LLC. We specialize mostly in planting trees and stone work, some water features. We would like to see design themes that include a tree or trees and a stone walkway or wall. We like earth tone colors. We like traditional to modern designs.

Target Market(s)

Homeowners

Industry/Entity Type

Landscape

Contact Information for Business Card

Nature themed design, earth tone colors, space for company name, address, phone numbers, email and website address

Logo Text

No text

Font styles to use
Serif

Colors

Designer to choose colors to be used in the design.

Requirements
Must have
• A tree or trees, similar to the ones uploaded in my supporting images
Nice to have
• I like trees similar to those in my uploaded supporting images. I like artistic, nature theme, earth tone colors
Should not have
• Pictures of real landscapes, cartoon looking logo or objects

```html
<!DOCTYPE html>
<html lang="en">
<head>
<meta charset="UTF-8">
<title>Belwick's Landscape and Design LLC – Business Card</title>
<link href="https://fonts.googleapis.com/css2?family=Abel&family=Josefin+Sans:wght@300;400&display=swap" rel="stylesheet">
<style>
  :root {
    --page-bg: #c9ccce;
    --card-teal: #27c194;
    --card-teal-deep: #1fae8c;
    --card-green: #4cd22c;
    --card-green-deep: #2fae22;
    --card-olive: #7f9c1c;
    --text-light: #ffffff;
  }
  html, body {
    margin: 0;
    padding: 0;
    width: 1200px;
    height: 801px;
    overflow: hidden;
    background: var(--page-bg);
  }
  .business-card {
    position: absolute;
    left: 75px;
    top: 100px;
    width: 1050px;
    height: 600px;
    overflow: hidden;
    background: var(--card-teal);
    box-shadow: 0 10px 30px rgba(0,0,0,0.18);
  }
  .card-shapes {
    position: absolute;
    inset: 0;
    width: 100%;
    height: 100%;
  }
  .brand-mark {
    position: absolute;
    left: 169px;
    top: 44px;
    width: 244px;
    height: 244px;
    border-radius: 50%;
    border: 5px solid rgba(255,255,255,0.85);
    box-sizing: border-box;
  }
  .company-name {
    position: absolute;
    left: 19px;
    top: 278px;
    margin: 0;
    font-family: "Abel", sans-serif;
    font-weight: 400;
    font-size: 39px;
    color: var(--text-light);
    white-space: nowrap;
  }
  .office-details {
    position: absolute;
    right: 46px;
    top: 50px;
    text-align: right;
    font-family: "Josefin Sans", sans-serif;
    font-size: 19px;
    line-height: 27px;
    color: var(--text-light);
  }
  .person {
    position: absolute;
    left: 630px;
    top: 330px;
    font-family: "Josefin Sans", sans-serif;
    color: var(--text-light);
  }
  .person-name {
    margin: 0;
    font-size: 52px;
    line-height: 56px;
    letter-spacing: 1px;
    font-weight: 400;
    white-space: nowrap;
  }
  .person-name .surname { font-weight: 300; }
  .person-role {
    margin: 0;
    font-size: 25px;
    font-weight: 300;
    line-height: 30px;
  }
  .contact-list {
    list-style: none;
    margin: 28px 0 0;
    padding: 0;
    font-size: 19px;
    line-height: 33px;
    white-space: nowrap;
  }
</style>
</head>
<body>
  <div class="business-card">
    <svg class="card-shapes" viewBox="0 0 1050 600" preserveAspectRatio="none" aria-hidden="true">
      <defs>
        <linearGradient id="greenBand" x1="0" y1="1" x2="1" y2="0">
          <stop offset="0" stop-color="var(--card-green-deep)"/>
          <stop offset="0.6" stop-color="var(--card-green)"/>
        </linearGradient>
      </defs>
      <path d="M0 0 H1050 V600 H0 Z" fill="var(--card-teal)"/>
      <path d="M0 380 C200 420 360 520 430 600 H0 Z" fill="var(--card-teal-deep)" opacity="0.45"/>
      <path d="M185 600 C330 380 600 230 1050 170 V600 Z" fill="url(#greenBand)"/>
      <path d="M487 0 H1050 V470 C980 300 800 130 487 0 Z" fill="var(--card-olive)" opacity="0.88"/>
    </svg>
    <div role="img" aria-label="Soft illustration of green leaves in the card background"
         style="position:absolute;left:520px;top:160px;width:420px;height:360px;border-radius:50%;background:radial-gradient(ellipse at center, rgba(40,150,40,0.35), rgba(40,150,40,0) 70%);"></div>

    <div class="brand-mark" aria-hidden="true"></div>
    <h1 class="company-name">Belwick's Landscape and Design LLC</h1>

    <div class="office-details">
      <div>Lot 12, Cedar Row, Brookhaven</div>
      <div>742 5-310</div>
    </div>

    <div class="person">
      <h2 class="person-name">EVAN <span class="surname">MARLOW</span></h2>
      <p class="person-role">Graphic Designer</p>
      <ul class="contact-list">
        <li>0917 4820 536</li>
        <li>Unit 3, Alder Lane, Fernmoor</li>
        <li>emarlow.studio@mailbox.com</li>
        <li>www.evanmarlow-design.com</li>
      </ul>
    </div>
  </div>
</body>
</html>
```